Kelvor Engineers: Why you should hire us keepsake

New design. Open to plastic cards. We are an engineering firm that designs cell phone towers and commercial buildings. Please check out our website www.kelvorstruct.com for more details. We want people to remember our card and for it to be useful if possible. We want the same look and feel on these cards to be translated to other marketing material we may need such as brochures.

Target Market(s)

Architects, Developers and Telecommunication Carriers

Industry/Entity Type

Engineering

Contact Information for Business Card

Card with our company colors, logo, and innovative design with elements related to our industry.

Font styles to use
Sans Serif

Colors
9bcb3c
abd036
0255a3

Requirements
Must have
• Sleek and hip design
Nice to have
• Bright lime green and navy coloring that pops with an innovative design.
Should not have
• A basic and boring design

```html
<!DOCTYPE html>
<html lang="en">
<head>
<meta charset="UTF-8">
<title>Kelvor Engineers – Business Card</title>
<link rel="stylesheet" href="https://fonts.googleapis.com/css2?family=Roboto:wght@400;700;900&family=Roboto+Condensed:wght@500&display=swap">
<style>
  :root {
    --backdrop: #1c1c1c;
    --paper: #f2f2f2;
    --lime: #05f505;
    --navy: #032b58;
    --white: #ffffff;
  }
  * { margin: 0; padding: 0; box-sizing: border-box; }
  html, body {
    width: 1200px;
    height: 960px;
    overflow: hidden;
    background: var(--backdrop);
    font-family: "Roboto", Arial, sans-serif;
  }
  .card {
    position: absolute;
    width: 600px;
    height: 343px;
    overflow: hidden;
  }
  .card--front { left: 314px; top: 113px; background: var(--paper); }
  .card--back  { left: 311px; top: 472px; background: var(--navy); }

  .card__band { position: absolute; inset: 0; }

  .wordmark {
    position: absolute;
    left: 0;
    right: 0;
    text-align: center;
    font-family: "Roboto", Arial, sans-serif;
    font-weight: 900;
    color: var(--lime);
    letter-spacing: -2px;
    line-height: 1;
  }
  .card--front .wordmark { top: 30px; font-size: 80px; color: var(--navy); }
  .card--back .wordmark  { top: 114px; font-size: 106px; }

  .contact {
    position: absolute;
    left: 0;
    right: 0;
    top: 250px;
    text-align: center;
    color: var(--white);
  }
  .contact__name {
    font-family: "Roboto Condensed", Arial, sans-serif;
    font-weight: 500;
    font-size: 21px;
    text-transform: uppercase;
    margin-bottom: 6px;
  }
  .contact__line { font-size: 14px; line-height: 20px; }

  .tagline {
    position: absolute;
    left: 0;
    right: 0;
    top: 266px;
    display: flex;
    align-items: center;
    justify-content: center;
    gap: 3px;
    color: var(--lime);
    font-weight: 700;
    font-size: 15px;
  }
  .tagline::before, .tagline::after {
    content: "";
    width: 30px;
    height: 1.5px;
    background: var(--white);
  }
  .offices {
    position: absolute;
    left: 0;
    right: 0;
    top: 287px;
    text-align: center;
    color: var(--white);
    font-size: 15px;
    letter-spacing: 0.5px;
  }
</style>
</head>
<body>
  <section class="card card--front">
    <svg class="card__band" width="600" height="343" viewBox="0 0 600 343" aria-hidden="true">
      <polygon points="0,0 300,229 600,0 600,228 450,343 148,343 0,230" fill="var(--lime)"/>
      <polyline points="0,0 300,229 600,0" fill="none" stroke="var(--navy)" stroke-width="2.5"/>
      <line x1="0" y1="230" x2="148" y2="343" stroke="var(--navy)" stroke-width="2.5"/>
      <line x1="600" y1="228" x2="450" y2="343" stroke="var(--navy)" stroke-width="2.5"/>
    </svg>
    <div class="wordmark">Kelvor</div>
    <div class="contact">
      <p class="contact__name">Dana Holloway Reyes</p>
      <p class="contact__line">P: 404.555.0148 M: 470.555.0193 E: dreyes@kelvorstruct.com</p>
      <p class="contact__line">www.kelvorstruct.com</p>
    </div>
  </section>

  <section class="card card--back">
    <div class="wordmark">Kelvor</div>
    <p class="tagline">MULTI-DISCIPLINE ENGINEERING</p>
    <p class="offices">Atlanta | Charlotte | Houston | San Antonio</p>
  </section>
</body>
</html>
```